The Linen Loft Co

We need a business card design for our wardrobe company.
Please visit our website www.gentlelinenlofts.com to get an idea of who we are.

```html
<!DOCTYPE html>
<html lang="en">
<head>
<meta charset="utf-8">
<title>The Linen Loft Co – Business Card</title>
<link rel="stylesheet" href="https://fonts.googleapis.com/css2?family=Arimo:wght@700&family=Jost:wght@300;400&display=swap">
<style>
  :root {
    --backdrop: #d6d6d6;
    --card-white: #f3f3f3;
    --card-black: #000000;
    --gold: #c08a14;
    --ink: #111111;
    --paper-text: #ffffff;
    --muted: #c9c9c9;
  }
  html, body {
    margin: 0;
    padding: 0;
    width: 1125px;
    height: 1200px;
    overflow: hidden;
    background: var(--backdrop);
  }
  .canvas {
    position: relative;
    width: 1125px;
    height: 1200px;
  }
  .card {
    position: absolute;
    left: 150px;
    width: 825px;
    height: 471px;
    box-shadow: 2px 3px 5px rgba(0,0,0,0.35);
    overflow: hidden;
  }
  .card-front {
    top: 98px;
    background: linear-gradient(135deg, #f8f8f8 0%, var(--card-white) 50%, #e9e9e9 100%);
  }
  .card-back {
    top: 631px;
    background: var(--card-black);
  }
  .front-brand {
    position: absolute;
    left: 0;
    top: 224px;
    width: 442px;
    text-align: center;
    font-family: "Arimo", Arial, sans-serif;
    font-weight: 700;
    color: var(--ink);
  }
  .front-brand .brand-name {
    font-size: 27px;
    letter-spacing: -0.3px;
    margin: 0;
    line-height: 1;
    text-transform: uppercase;
  }
  .front-brand .tagline {
    font-size: 24px;
    margin: 18px 0 0;
    line-height: 1;
  }
  .contact-panel {
    position: absolute;
    left: 436px;
    top: 101px;
    width: 389px;
    height: 299px;
    background: var(--card-black);
    box-shadow: -3px 4px 10px rgba(0,0,0,0.3);
    font-family: "Jost", "Futura", sans-serif;
    color: var(--paper-text);
  }
  .person-name {
    position: absolute;
    left: 40px;
    top: 32px;
    margin: 0;
    font-weight: 400;
    font-size: 32px;
    color: var(--gold);
    line-height: 1;
  }
  .person-role {
    position: absolute;
    left: 40px;
    top: 68px;
    margin: 0;
    font-size: 20px;
    font-weight: 400;
    color: var(--muted);
  }
  .address {
    position: absolute;
    left: 38px;
    top: 119px;
    margin: 0;
    font-style: normal;
    font-size: 19px;
    font-weight: 300;
    line-height: 25px;
  }
  .contact-list {
    position: absolute;
    left: 38px;
    top: 183px;
    margin: 0;
    padding: 0;
    list-style: none;
    font-size: 19px;
    font-weight: 300;
    line-height: 25px;
  }
  .contact-list li {
    display: flex;
    align-items: center;
  }
  .contact-list svg {
    width: 17px;
    height: 17px;
    margin-right: 10px;
    fill: var(--gold);
    flex: none;
  }
  .back-brand {
    position: absolute;
    left: 0;
    top: 40px;
    width: 825px;
    height: 431px;
    display: flex;
    align-items: center;
    justify-content: center;
    gap: 22px;
    font-family: "Arimo", Arial, sans-serif;
    font-weight: 700;
    color: var(--gold);
  }
  .back-brand .mark {
    width: 80px;
    height: 80px;
    background: var(--gold);
  }
  .back-brand .brand-text {
    text-align: center;
  }
  .back-brand .brand-name {
    font-size: 26px;
    margin: 0;
    line-height: 1;
    text-transform: uppercase;
  }
  .back-brand .tagline {
    font-size: 23px;
    margin: 14px 0 0;
    line-height: 1;
  }
</style>
</head>
<body>
<main class="canvas">
  <section class="card card-front" aria-label="Card front">
    <div class="front-brand">
      <p class="brand-name">The Linen Loft Co</p>
      <p class="tagline">Rest Easy, Stored Neatly</p>
    </div>
    <div class="contact-panel">
      <h1 class="person-name">Daniel Hartley</h1>
      <p class="person-role">President</p>
      <address class="address">Marlow House, 42 Fennel Street,<br>London EC2A 4QT</address>
      <ul class="contact-list">
        <li>
          <svg viewBox="0 0 24 24" aria-hidden="true"><path d="M6.6 10.8a15.1 15.1 0 0 0 6.6 6.6l2.2-2.2a1 1 0 0 1 1-.25 11.4 11.4 0 0 0 3.6.57 1 1 0 0 1 1 1V20a1 1 0 0 1-1 1A17 17 0 0 1 3 4a1 1 0 0 1 1-1h3.5a1 1 0 0 1 1 1c0 1.25.2 2.45.57 3.57a1 1 0 0 1-.25 1z"/></svg>
          020 7946 0821
        </li>
        <li>
          <svg viewBox="0 0 24 24" aria-hidden="true"><path d="M2 6h20v12H2z M2 6l10 7 10-7" fill="none" stroke="#c08a14" stroke-width="2"/></svg>
          info@gentlelinenlofts.com
        </li>
        <li>
          <svg viewBox="0 0 24 24" aria-hidden="true"><circle cx="12" cy="12" r="10"/><path d="M8 5c2 2 0 4 2 5s3 3 1 5M16 8c-2 1-1 3 1 4s1 4-1 6" fill="none" stroke="#000" stroke-width="1.6"/></svg>
          www.gentlelinenlofts.com
        </li>
      </ul>
    </div>
  </section>

  <section class="card card-back" aria-label="Card back">
    <div class="back-brand">
      <div class="mark" aria-hidden="true"></div>
      <div class="brand-text">
        <p class="brand-name">The Linen Loft Co</p>
        <p class="tagline">Rest Easy, Stored Neatly</p>
      </div>
    </div>
  </section>
</main>
</body>
</html>
```